List Now, Launch Later - DL Flyer front & back

Looking for a flyer that has nothing much other than “List Now, Launch Later” on the front with text to fill the back. With image on front that symbolises launch, maybe house being launch like a rocket.
The text has yet to be written but here is the gist: This is for the back of flyer.
List property and delay the launch. In the meantime, we can:
· Prepare contract
· Prepare marketing
· Prepare the property
· Do the Pest and Building Report
· Give the tenants their due notice of sale
· Advise buyers in an off market capacity
This ensures we are first to market when the time comes rather than coming onto the market along with a surge of spring sellers. Buyers are still buying now. The lack of stock is inadvertently creating strength in the market.
The feel has to be modern, clean, contemporary & graphic

```html
<!DOCTYPE html>
<html lang="en">
<head>
<meta charset="utf-8">
<title>List Now, Launch Later – DL Flyer</title>
<link href="https://fonts.googleapis.com/css2?family=Montserrat:wght@300;400;500;600;700;800&display=swap" rel="stylesheet">
<style>
  :root{
    --orange:#f7ad3b;
    --black:#0a0a0a;
    --white:#ffffff;
    --paper:#ffffff;
    --photo-top:#d8d8d6;
    --photo-mid:#c4c2be;
    --photo-floor:#8c6b4b;
    --emblem-grey:#dcdcdc;
  }
  *{box-sizing:border-box;margin:0;padding:0}
  html,body{width:805px;height:1200px;overflow:hidden;background:var(--paper)}
  body{position:relative;font-family:"Montserrat",sans-serif}

  .flyer{position:absolute;width:361px;height:511px;overflow:hidden}
  .theme-dark{--veil:rgba(8,8,8,.93);--band:#030303;--ink:var(--white);--rule:var(--white);--line:rgba(255,255,255,.75)}
  .theme-light{--veil:rgba(238,238,238,.86);--band:rgba(185,185,185,.45);--ink:#111;--rule:var(--orange);--line:rgba(0,0,0,.55)}

  .photo{position:absolute;inset:0;
    background:linear-gradient(180deg,var(--photo-top) 0%,var(--photo-mid) 55%,#b5b0a8 82%,var(--photo-floor) 100%)}
  .veil{position:absolute;background:var(--veil)}
  .flyer--front .veil{left:31px;top:0;width:330px;height:465px}
  .flyer--back.theme-dark .veil{left:0;top:0;width:340px;height:468px}
  .flyer--back.theme-light .veil{left:0;top:0;width:351px;height:462px}

  .brand{position:absolute;width:88px;height:88px;border-radius:50%;background:var(--white);
    display:flex;justify-content:center;font-weight:700;font-size:8px;letter-spacing:.08em;color:#111}
  .brand--top{left:94px;top:-55px;align-items:flex-end;padding-bottom:18px}
  .brand--bottom{left:137px;top:478px;align-items:flex-start;padding-top:14px}

  .emblem{position:absolute;border-radius:28px;
    background:radial-gradient(circle at 18% 78%,var(--orange) 0 22%,transparent 23%),
               linear-gradient(135deg,var(--emblem-grey),#f2f2f2 60%,#bdbdbd)}
  .theme-light .emblem{background:radial-gradient(circle at 18% 78%,var(--orange) 0 22%,transparent 23%),
               linear-gradient(135deg,#9a9a9a,#5c5c5c 60%,#3a3a3a)}
  .flyer--front .emblem{left:92px;top:90px;width:123px;height:133px}
  .flyer--back .emblem{left:177px;top:-24px;width:128px;height:124px;opacity:.9}

  .headline-band{position:absolute;left:60px;top:337px;width:301px;height:79px;background:var(--band)}
  .rule{position:absolute;height:2px;background:var(--rule)}
  .flyer--front .rule{left:97px;top:332px;width:71px}
  .headline{position:absolute;left:97px;top:350px;color:var(--ink);line-height:1}
  .headline__main{display:block;font-weight:800;font-size:36px;letter-spacing:-.01em}
  .headline__sub{display:block;margin-top:6px;font-weight:400;font-size:19.5px;letter-spacing:.12em}
  .arrow{position:absolute;left:322px;top:365px;width:0;height:0;
    border-top:14.5px solid transparent;border-bottom:14.5px solid transparent;border-left:15px solid var(--orange)}

  /* back */
  .title{position:absolute;right:31px;top:144px;text-align:right;color:var(--ink);line-height:1.1}
  .theme-light .title{right:37px}
  .title__main{display:block;font-weight:700;font-size:21px}
  .title__sub{display:block;font-weight:300;font-size:20px}
  .title-rule{position:absolute;right:31px;top:200px;width:94px;height:1.5px;background:var(--orange)}
  .theme-light .title-rule{right:37px}
  .pitch{position:absolute;right:31px;top:210px;width:96px;text-align:right;color:var(--ink)}
  .theme-light .pitch{right:37px}
  .pitch h2{font-size:9.5px;font-weight:700;margin-bottom:4px}
  .pitch p{font-size:5.4px;line-height:1.22;font-weight:400;margin-bottom:4px}

  .tasks{position:absolute;left:26px;top:247px;width:144px;color:var(--ink)}
  .tasks h2{font-size:9.5px;font-weight:700;padding-bottom:5px;border-bottom:1px solid var(--orange)}
  .tasks ul{list-style:none}
  .tasks li{display:flex;justify-content:space-between;align-items:center;height:12.6px;
    font-size:6.6px;font-weight:400;border-bottom:.6px solid var(--line)}
  .tasks svg{width:10px;height:10px;stroke:var(--ink);fill:none;stroke-width:1.4}

  .agent{position:absolute;left:26px;top:366px;color:var(--ink)}
  .agent__name{font-size:10.5px;font-weight:700}
  .agent__role{font-size:7px;font-weight:400;margin-top:2px}
  .socials{display:flex;gap:2.5px;margin-top:5px}
  .socials span{width:10.5px;height:10.5px;border-radius:50%;background:var(--orange)}
  .contact{list-style:none;margin-top:8px;width:89px;border-top:.6px solid var(--line)}
  .contact li{display:flex;align-items:center;gap:3px;font-size:4.6px;height:8.4px;border-bottom:.6px solid var(--line)}
  .contact svg{width:5px;height:5px;fill:var(--ink)}

  .services{position:absolute;left:195px;top:376px;display:grid;grid-template-columns:repeat(3,39px);gap:0 9px;row-gap:10px}
  .theme-light .services{left:174px;top:376px;grid-template-columns:repeat(3,44px);gap:0 9px;row-gap:10px}
  .service{border-top:.8px solid var(--line);padding-top:2px;color:var(--ink)}
  .service span{display:block;font-size:3.8px;letter-spacing:.06em;font-weight:500}
  .service svg{display:block;margin-top:3px;width:17px;height:17px;fill:none;stroke:var(--orange);stroke-width:1.3}
</style>
</head>
<body>

<svg width="0" height="0" style="position:absolute" aria-hidden="true">
  <defs>
    <symbol id="i-folder" viewBox="0 0 20 20"><path d="M2 5h6l2 2h8v10H2z"/><path d="M2 9h16"/></symbol>
    <symbol id="i-magnet" viewBox="0 0 20 20"><path d="M4 3v8a6 6 0 0 0 12 0V3h-4v8a2 2 0 0 1-4 0V3z"/><path d="M4 7h4M12 7h4"/></symbol>
    <symbol id="i-tag" viewBox="0 0 20 20"><path d="M11 2h7v7l-9 9-7-7z"/><circle cx="14.5" cy="5.5" r="1.3"/></symbol>
    <symbol id="i-award" viewBox="0 0 20 20"><circle cx="10" cy="8" r="5.5"/><path d="M6 12l-2 6 3-1 2 2 1-5M14 12l2 6-3-1-2 2-1-5"/></symbol>
    <symbol id="i-note" viewBox="0 0 20 20"><path d="M2 3h16v11H8l-4 4v-4H2z"/><path d="M5 7h10M5 10h8"/></symbol>
    <symbol id="i-chat" viewBox="0 0 20 20"><path d="M2 9c0-4 3-6 7-6s7 2 7 6-3 6-7 6c-1 0-2 0-3-.5L3 16l1-3C2.5 12 2 10.5 2 9z"/></symbol>
    <symbol id="i-chats" viewBox="0 0 20 20"><path d="M1 7c0-3 2.5-5 6-5s6 2 6 5-2.5 5-6 5c-1 0-1.6 0-2.4-.3L2 13l.8-2.4C1.6 9.7 1 8.5 1 7z"/><path d="M14 7.5c3 .3 5 2 5 4.5 0 1.2-.5 2.2-1.5 3l.8 2.5-2.8-1.2c-.8.3-1.5.3-2.5.3-2.5 0-4.5-1.2-5.2-3"/></symbol>
    <symbol id="i-phone" viewBox="0 0 10 10"><path d="M2 1l2 2-1 1.2c.8 1.4 1.6 2.2 2.8 2.8L7 6l2 2-1.2 1.5C4.5 9 1 5.5.5 2.2z"/></symbol>
    <symbol id="i-mail" viewBox="0 0 10 10"><path d="M0 2h10v6H0z"/></symbol>
    <symbol id="i-pin" viewBox="0 0 10 10"><path d="M5 0a3.5 3.5 0 0 1 3.5 3.5C8.5 6 5 10 5 10S1.5 6 1.5 3.5A3.5 3.5 0 0 1 5 0z"/></symbol>
  </defs>
</svg>

<!-- Front, dark -->
<section class="flyer flyer--front theme-dark" style="left:15px;top:17px">
  <div class="photo" role="img" aria-label="Photo of a bright living room with fireplace and timber floor"></div>
  <div class="veil"></div>
  <div class="brand brand--top">KEYLINE</div>
  <div class="emblem" role="img" aria-label="Emblem of a house shape lifting off like a rocket"></div>
  <div class="headline-band"></div>
  <span class="rule"></span>
  <h1 class="headline"><span class="headline__main">LIST NOW</span><span class="headline__sub">LAUNCH LATER</span></h1>
  <span class="arrow"></span>
</section>

<!-- Back, dark -->
<section class="flyer flyer--back theme-dark" style="left:428px;top:17px">
  <div class="photo" role="img" aria-label="Photo of a bright living room with fireplace and timber floor"></div>
  <div class="veil"></div>
  <div class="emblem" role="img" aria-label="Emblem of a house shape lifting off like a rocket"></div>
  <h1 class="title"><span class="title__main">List Property,</span><span class="title__sub">and Delay the Launch</span></h1>
  <span class="title-rule"></span>
  <div class="pitch">
    <h2>Beat the Rush.</h2>
    <p>This ensures we are first to market when the time comes rather than coming onto the market along with a surge of spring sellers.</p>
    <p>Buyers are still buying now. The lack of stock is incidentally creating strength in the market now that you can take advantage of.</p>
  </div>
  <div class="tasks">
    <h2>In the meantime we’ll:</h2>
    <ul>
      <li>Prepare the contract<svg><use href="#i-folder"/></svg></li>
      <li>Prepare marketing for the Property<svg><use href="#i-magnet"/></svg></li>
      <li>Prepare the property for sale<svg><use href="#i-tag"/></svg></li>
      <li>Do the Pest and Building Report<svg><use href="#i-award"/></svg></li>
      <li>Give the tenants their due notice of sale<svg><use href="#i-note"/></svg></li>
      <li>Advice buyers in an off-market capacity<svg><use href="#i-chat"/></svg></li>
    </ul>
  </div>
  <div class="agent">
    <p class="agent__name">firstname surname</p>
    <p class="agent__role">real estate consultant</p>
    <div class="socials"><span></span><span></span><span></span></div>
    <ul class="contact">
      <li><svg><use href="#i-phone"/></svg>+005120048617</li>
      <li><svg><use href="#i-mail"/></svg>firstname.surname@keyline.au</li>
      <li><svg><use href="#i-pin"/></svg>cityname, region, australia</li>
    </ul>
  </div>
  <div class="services">
    <div class="service"><span>CONTRACT</span><svg><use href="#i-folder"/></svg></div>
    <div class="service"><span>SALE PREPPING</span><svg><use href="#i-tag"/></svg></div>
    <div class="service"><span>TENANT NOTICE</span><svg><use href="#i-note"/></svg></div>
    <div class="service"><span>MARKETING</span><svg><use href="#i-magnet"/></svg></div>
    <div class="service"><span>CERTIFICATIONS</span><svg><use href="#i-award"/></svg></div>
    <div class="service"><span>BUYER ADVISORY</span><svg><use href="#i-chats"/></svg></div>
  </div>
  <div class="brand brand--bottom">KEYLINE</div>
</section>

<!-- Front, light -->
<section class="flyer flyer--front theme-light" style="left:15px;top:623px">
  <div class="photo" role="img" aria-label="Photo of a bright living room with fireplace and timber floor"></div>
  <div class="veil"></div>
  <div class="brand brand--top">KEYLINE</div>
  <div class="emblem" role="img" aria-label="Emblem of a house shape lifting off like a rocket"></div>
  <div class="headline-band"></div>
  <span class="rule"></span>
  <h1 class="headline"><span class="headline__main">LIST NOW</span><span class="headline__sub">LAUNCH LATER</span></h1>
  <span class="arrow"></span>
</section>

<!-- Back, light -->
<section class="flyer flyer--back theme-light" style="left:428px;top:623px">
  <div class="photo" role="img" aria-label="Photo of a bright living room with fireplace and timber floor"></div>
  <div class="veil"></div>
  <div class="emblem" role="img" aria-label="Emblem of a house shape lifting off like a rocket"></div>
  <h1 class="title"><span class="title__main">List Property,</span><span class="title__sub">and Delay the Launch</span></h1>
  <span class="title-rule"></span>
  <div class="pitch">
    <h2>Beat the Rush.</h2>
    <p>This ensures we are first to market when the time comes rather than coming onto the market along with a surge of spring sellers.</p>
    <p>Buyers are still buying now. The lack of stock is incidentally creating strength in the market now that you can take advantage of.</p>
  </div>
  <div class="tasks" style="width:150px">
    <h2>In the meantime we’ll:</h2>
    <ul>
      <li>Prepare the contract<svg><use href="#i-folder"/></svg></li>
      <li>Prepare marketing for the Property<svg><use href="#i-magnet"/></svg></li>
      <li>Prepare the property for sale<svg><use href="#i-tag"/></svg></li>
      <li>Do the Pest and Building Report<svg><use href="#i-award"/></svg></li>
      <li>Give the tenants their due notice of sale<svg><use href="#i-note"/></svg></li>
      <li>Advice buyers in an off-market capacity<svg><use href="#i-chat"/></svg></li>
    </ul>
  </div>
  <div class="agent">
    <p class="agent__name">firstname surname</p>
    <p class="agent__role">real estate consultant</p>
    <div class="socials"><span></span><span></span><span></span></div>
    <ul class="contact">
      <li><svg><use href="#i-phone"/></svg>+005120048617</li>
      <li><svg><use href="#i-mail"/></svg>firstname.surname@keyline.au</li>
      <li><svg><use href="#i-pin"/></svg>cityname, region, australia</li>
    </ul>
  </div>
  <div class="services">
    <div class="service"><span>CONTRACT</span><svg><use href="#i-folder"/></svg></div>
    <div class="service"><span>SALE PREPPING</span><svg><use href="#i-tag"/></svg></div>
    <div class="service"><span>TENANT NOTICE</span><svg><use href="#i-note"/></svg></div>
    <div class="service"><span>MARKETING</span><svg><use href="#i-magnet"/></svg></div>
    <div class="service"><span>CERTIFICATIONS</span><svg><use href="#i-award"/></svg></div>
    <div class="service"><span>BUYER ADVISORY</span><svg><use href="#i-chats"/></svg></div>
  </div>
  <div class="brand brand--bottom">KEYLINE</div>
</section>

</body>
</html>
```